Diverse, up-scale salon needs eye-catching, unique business cards.

We are looking for a unique business card design for our stylist but that can also be multi functional and used for appointment reminder and referrals. I will need a design in a format that I can modify names and titles going forward. In the past we have had a dark background with the logo on one side, and stylist and contact information on the other but we are open to all ideas. I have included our mission statement as well as branded colors below. The statement doesn't need to go on the card, it's just a reference for target market. We need space for the stylists name, title, instagram handle and then the salons phone number, website and address. I am also open to adding a spot for a qr code linked to the stylist instagram or the salon booking link.

primary brand colors:
#333333 #233415 #36502a #93874a #000000
Mission statement:
Vessolin Hair Studio, a high-end salon located in the lively Downtown Farmington, Michigan, is committed to providing exceptional services in a welcoming and relaxed environment to meet the needs of our diverse clientele.
Our salon specializes in contemporary custom haircuts, coloring, extensions, and barbering and beard grooming services. Our team of skilled stylists is passionate and inventive in their hair styling techniques. At the heart of our salon are values centered on quality, innovation, creativity, and above all, comfort. These core values are evident in every appointment across our customizable array of services.
Our goal is to establish a benchmark for exceptional hair care for every human.
Website: www.vessolinhairstudio.example
instagram: @vessolinhairstudio
address: 41782 Pelham Crest Rd, Farmington MI
phone: 248-613-4087

Industry/Entity Type

Hair Salon

Contact Information for Business Card

Stylist name, title, phone, instagram, website, address, (optional qr code)

Requirements
Should not have
• Does not need mission statement on the card.

```html
<!DOCTYPE html>
<html lang="en">
<head>
<meta charset="utf-8">
<title>Vessolin Hair Studio — Business Card</title>
<link rel="stylesheet" href="https://fonts.googleapis.com/css2?family=Cinzel:wght@400;500&family=Montserrat:wght@400;500&display=swap">
<style>
  :root {
    --backdrop: #3a3a3a;
    --card: #141414;
    --gold: #93874a;
    --gold-line: #7d7340;
    --ink-light: #eeeeee;
    --silver: #8f8f8f;
  }
  * { box-sizing: border-box; margin: 0; padding: 0; }
  html, body {
    width: 1200px; height: 801px; overflow: hidden;
    background: var(--backdrop);
  }
  .stage {
    position: relative; width: 1200px; height: 801px;
    display: flex; align-items: center; justify-content: center; gap: 40px;
  }
  .card {
    position: relative; width: 540px; height: 309px;
    background: var(--card);
    border: 1.5px solid var(--gold);
    box-shadow: 0 14px 30px rgba(0,0,0,.35);
    font-family: "Montserrat", sans-serif;
  }

  /* Front face */
  .brand-seal {
    position: absolute; left: 34px; top: 26px;
    width: 150px; height: 150px;
    border: 2px solid var(--gold); border-radius: 50%;
    display: flex; align-items: center; justify-content: center;
    text-align: center;
  }
  .brand-name {
    font-family: "Montserrat", sans-serif; font-weight: 500;
    color: var(--gold); font-size: 15px; letter-spacing: 2px;
    line-height: 1.4; text-transform: uppercase;
  }
  .stylist {
    position: absolute; right: 34px; top: 40px; text-align: right;
  }
  .stylist-name {
    font-family: "Cinzel", serif; font-weight: 500;
    color: var(--gold); font-size: 24px; letter-spacing: 1.5px;
  }
  .stylist-title {
    color: var(--ink-light); font-size: 14px; margin-top: 0px;
  }
  .divider {
    position: absolute; left: 34px; right: 34px; top: 188px;
    height: 1px; background: var(--gold-line);
  }
  .contact-list {
    position: absolute; left: 34px; top: 206px; list-style: none;
  }
  .contact-list li {
    display: flex; align-items: center; gap: 9px;
    color: var(--ink-light); font-size: 14.5px; line-height: 26px;
  }
  .contact-list svg { width: 13px; height: 13px; flex: none; }
  .address {
    position: absolute; right: 34px; top: 96px; text-align: right;
    color: var(--ink-light); font-size: 15px; line-height: 23px;
  }

  /* Back face */
  .card-back { display: flex; align-items: center; justify-content: center; }
  .back-seal {
    width: 200px; height: 200px; border-radius: 50%;
    border: 3px solid var(--silver);
    display: flex; align-items: center; justify-content: center; text-align: center;
  }
  .back-seal .brand-name { color: var(--silver); font-size: 19px; letter-spacing: 3px; }
</style>
</head>
<body>
<main class="stage">
  <section class="card card-front" aria-label="Business card front">
    <div class="brand-seal"><span class="brand-name">Vessolin<br>Hair Studio</span></div>
    <div class="stylist">
      <p class="stylist-name">MARISOL</p>
      <p class="stylist-title">President</p>
    </div>
    <address class="address" style="font-style:normal">41782 Pelham Crest Rd<br>Farmington MI</address>
    <div class="divider"></div>
    <ul class="contact-list">
      <li>
        <svg viewBox="0 0 16 16" aria-hidden="true"><path fill="#93874a" d="M3.5 1.5 6 4 4.8 5.8c.8 1.9 2.4 3.5 4.4 4.4L11 9l2.5 2.5-1.7 2.2C6.6 13.4 2.6 9.4 1.3 3.2z"/></svg>
        248-613-4087
      </li>
      <li>
        <svg viewBox="0 0 16 16" aria-hidden="true"><circle cx="8" cy="8" r="6" fill="#93874a"/></svg>
        @vessolinhairstudio
      </li>
      <li>
        <svg viewBox="0 0 16 16" aria-hidden="true"><g fill="none" stroke="#93874a" stroke-width="1.5"><circle cx="8" cy="8" r="6.5"/><ellipse cx="8" cy="8" rx="2.8" ry="6.5"/><path d="M1.5 8h13"/></g></svg>
        www.vessolinhairstudio.example
      </li>
    </ul>
  </section>

  <section class="card card-back" aria-label="Business card back">
    <div class="back-seal"><span class="brand-name">Vessolin<br>Hair Studio</span></div>
  </section>
</main>
</body>
</html>
```